creation of a business card design for a company specializing in the creation...

I would like to create a design for a professional business card on a black background and with the company's colors (I am attaching some files: including the logo in horizontal and centered format, I am also attaching a recent project design a T-shirt, this is the one I chose to give you an idea of my preferences.

we are in the process of developing a new website design, it is still in the development phase but it can be viewed at the following address: www.vantrelmo.be to give you other ideas about the company
you will see for yourself the subject of my main activity: company specializing in the construction of stairs

I would like a business card that stands out from the rest with a unique design

here is the informations
Name: Lucien Barthel
Function: Manager
Address: Rue Moulinet du Parc 42
7180 La Louvière
telephone: +32 468 219 804
email: info@rx7p.be
website: rx7p. be
social networks: Facebook, YouTube, TikTok, Instagram

Target Market(s)

customer who wants to have a beautiful staircase built

Industry/Entity Type

contruction d'escalier

Contact Information for Business Card

Adresse. Numero de telephone, site web, le texte : "Createur d'escalier", logo recto-verso, icone des reseaux sociaux

Requirements
Must have
• the mention: Stair creator
Nice to have
• an illustration of a designer staircase
Should not have
• do not distort the logo

```html
<!DOCTYPE html>
<html lang="fr">
<head>
<meta charset="utf-8">
<title>Vantrelmo – Cartes de visite</title>
<link rel="stylesheet" href="https://fonts.googleapis.com/css2?family=Open+Sans:wght@400;600;700&display=swap">
<style>
  :root{
    --stage:#2a2d33;
    --card:#141416;
    --card-edge:#0a0a0b;
    --accent:#6d9cc0;
    --steel:#8f9aa5;
    --ink:#f2f2f2;
    --muted:#c9ced4;
  }
  *{box-sizing:border-box;margin:0;padding:0}
  html,body{width:1200px;height:780px;overflow:hidden}
  body{
    background:var(--stage);
    font-family:"Open Sans",Arial,sans-serif;
    display:flex;align-items:center;justify-content:center;gap:36px;
  }
  .card{
    width:560px;height:320px;
    background:linear-gradient(160deg,#1c1c1f 0%,var(--card) 55%,var(--card-edge) 100%);
    border-radius:6px;position:relative;overflow:hidden;
    box-shadow:0 18px 40px rgba(0,0,0,.55);
    color:var(--ink);
  }
  /* front */
  .identity{position:absolute;left:34px;top:34px;padding-left:14px;border-left:6px solid var(--accent)}
  .identity__name{font-size:30px;font-weight:700;color:var(--accent);line-height:1.05}
  .identity__role{font-size:15px;color:var(--ink);margin-top:2px}
  .address{position:absolute;left:54px;top:118px;font-size:14.5px;line-height:1.4}
  .contacts{position:absolute;left:34px;top:168px;list-style:none;font-size:14.5px;line-height:1.55}
  .contacts li{display:flex;align-items:center;gap:8px}
  .contacts svg{width:13px;height:13px;fill:var(--muted);flex:none}
  .social{position:absolute;left:34px;bottom:26px;display:flex;align-items:center;gap:9px;font-size:17px}
  .social__dot{width:18px;height:18px;border-radius:50%;background:var(--steel)}
  /* brand name */
  .brand{position:absolute;display:flex;align-items:center;gap:12px}
  .brand__mark{border-radius:50%;background:var(--accent);flex:none}
  .brand__name{font-weight:600;color:var(--ink);line-height:1}
  .brand--front{right:34px;bottom:60px}
  .brand--front .brand__mark{width:26px;height:26px}
  .brand--front .brand__name{font-size:26px}
  .brand--back{left:50%;top:50%;transform:translate(-50%,-50%)}
  .brand--back .brand__mark{width:38px;height:38px}
  .brand--back .brand__name{font-size:40px}
</style>
</head>
<body>

<section class="card card--front" aria-label="Recto">
  <div class="identity">
    <p class="identity__name">Lucien Barthel</p>
    <p class="identity__role">Manager</p>
  </div>
  <p class="address">Rue Moulinet du Parc 42<br>7180 La Louvière</p>
  <ul class="contacts">
    <li><svg viewBox="0 0 24 24"><path d="M6.6 10.8a15 15 0 0 0 6.6 6.6l2.2-2.2a1 1 0 0 1 1-.25 11.4 11.4 0 0 0 3.6.57 1 1 0 0 1 1 1V20a1 1 0 0 1-1 1A17 17 0 0 1 3 4a1 1 0 0 1 1-1h3.5a1 1 0 0 1 1 1c0 1.25.2 2.45.57 3.57a1 1 0 0 1-.25 1z"/></svg>+32 468 219 804</li>
    <li><svg viewBox="0 0 24 24"><path d="M3 5h18v14H3zm2 2v.4l7 4.6 7-4.6V7zm0 2.8V17h14V9.8l-7 4.6z"/></svg>info@rx7p.be</li>
    <li><svg viewBox="0 0 24 24"><path d="M12 2a10 10 0 1 0 0 20 10 10 0 0 0 0-20zm0 2c.9 0 2.3 2 2.8 6H9.2C9.7 6 11.1 4 12 4zm-7.9 8h3.1c0 1.5.2 2.9.5 4H5.1a8 8 0 0 1-1-4zm1-2a8 8 0 0 1 3.9-5.3A14 14 0 0 0 7.2 10zm4.1 2h5.6c0 1.5-.2 2.9-.5 4H9.7a14 14 0 0 1-.5-4zm7.6 0h3.1a8 8 0 0 1-1 4h-2.6c.3-1.1.5-2.5.5-4zm0-2a14 14 0 0 0-1.9-5.3A8 8 0 0 1 19.9 10z"/></svg>www.rx7p.be</li>
  </ul>
  <div class="social">
    <span>Follow us:</span>
    <span class="social__dot"></span><span class="social__dot"></span><span class="social__dot"></span><span class="social__dot"></span>
  </div>
  <div class="brand brand--front">
    <span class="brand__mark"></span>
    <p class="brand__name">Vantrelmo</p>
  </div>
</section>

<section class="card card--back" aria-label="Verso">
  <div class="brand brand--back">
    <span class="brand__mark"></span>
    <p class="brand__name">Vantrelmo</p>
  </div>
</section>

</body>
</html>
```